Web and Logo Design for eCommerce site

We're launching a sister brand and require a full design for the site.

The site must have an established feel and appeal to corporate and institutional buyers.
Updates

Just a note about the wireframe design:

The Search & Rescue / Coast Guard / NVDK, etc. in the header area aren't buttons or menu items, but rather just info (along the lines of a tagline).  Sort of a "who we serve" sort of thing.

Worth noting is that it's specifically geared towards LARGE BUYERS.  For example, a police force buying 200 headlamps and 85 pairs of gloves.  So they'll register + sign in and then add a bunch of items to a RFQ.

Aim for a professional, masculine design.

Target Market(s)

We will be selling outdoor gear to the military, law enforcement, fire and rescue and first responders.

Requirements
Must have
• We require:
- Logo (vector based)

Site:
- template page
* main site template, re-skinned version of our current site
* horizontal drop-down menu
- product listings page
* thumbnail view of products
- product details page
* including elements such as product image, color/size selector, descriptions and specs (again, based loosely on our current website)
- account management page
* illustrating basic data entry styles for text box, buttons, grid, etc.

The site needs to be given a responsive design, so 2 versions of each design should be presented for desktop + mobile views.

Additional funds are available if the designer is able to fully implement the designs into a responsive framework such as bootstrap.

Nice to have
• Clean, professional design similar to:

http://military.trailvexagear.com/gov/accessories/gloves.html

http://leaf.ombrivo.com/ProductFind.aspx?language=EN&category=Hardshell&subcat=Waterproof_Jackets

```html
<!DOCTYPE html>
<html lang="en">
<head>
<meta charset="utf-8">
<title>KanVex – Outdoor Gear for First Responders</title>
<link href="https://fonts.googleapis.com/css2?family=Bree+Serif&family=Open+Sans:wght@400;600;700&family=Arimo:wght@400;700&display=swap" rel="stylesheet">
<style>
:root{
  --green:#66cc5e;
  --green-dark:#4caa44;
  --green-text:#3fae3a;
  --charcoal:#4b4b4b;
  --nav-active:#454545;
  --panel:#efefef;
  --border:#dcdcdc;
  --text:#333;
  --muted:#555;
  --white:#fff;
}
*{box-sizing:border-box;margin:0;padding:0}
html,body{width:1164px;height:1200px;overflow:hidden;background:var(--white)}
body{position:relative;font-family:"Arimo",Arial,sans-serif;color:var(--text)}
.abs{position:absolute}

/* Header */
.topbar{left:0;top:0;width:1164px;height:73px;background:var(--green)}
.brand{left:185px;top:15px;font-family:"Bree Serif",serif;font-size:34px;color:var(--white);line-height:1}
.login{left:546px;top:39px;font-family:"Open Sans",sans-serif;font-weight:600;font-size:13px;color:var(--white);display:flex;align-items:center;gap:5px}
.tagline{left:793px;top:20px;font-family:"Open Sans",sans-serif;font-weight:600;font-size:13.5px;line-height:19px;color:var(--white)}
.serve{left:0;top:73px;width:1164px;height:37px;background:var(--green-dark)}
.serve ul{list-style:none;display:flex;gap:9px;position:absolute;left:185px;top:11px;font-family:"Open Sans",sans-serif;font-size:11.7px;font-weight:600;color:var(--white)}
.mainnav{left:0;top:110px;width:1164px;height:36px;background:var(--green)}
.mainnav a{position:absolute;top:9px;font-family:"Open Sans",sans-serif;font-size:12.5px;color:var(--white);text-decoration:none}
.mainnav a.active{left:184px;top:8px;width:94px;height:22px;background:var(--nav-active);text-align:center;line-height:22px;border-bottom:2px solid #2e2e2e}

/* Slider */
.slider{left:182px;top:165px;width:800px;height:293px;border:1px solid #e4e4e4;border-radius:4px;box-shadow:0 0 3px rgba(0,0,0,.1);background:var(--white)}
.slide-photo{left:4px;top:4px;width:791px;height:284px;background:linear-gradient(180deg,#b9a88a 0%,#d8c496 38%,#a08a63 62%,#2a241c 78%,#1b1712 100%)}
.slide-label{left:4px;top:21px;width:145px;height:33px;background:rgba(255,255,255,.35);font-family:"Open Sans",sans-serif;font-weight:700;font-size:24px;color:var(--white);padding-left:20px;line-height:33px}
.arrow{top:290px}

/* Sidebar */
.sidebar{left:183px;top:488px;width:191px;height:362px;background:var(--panel);border:1px solid #e2e2e2;border-radius:3px}
.cat-title{left:183px;top:501px;width:191px;height:25px;background:repeating-linear-gradient(135deg,#4a4a4a 0 2px,#3d3d3d 2px 4px);font-size:16.5px;color:var(--white);text-align:center;line-height:25px}
.cat-list{left:208px;top:541px;width:150px;list-style:none;font-size:11.5px;color:var(--text)}
.cat-list li{height:28.3px;line-height:26px;border-bottom:1px solid #e2e2e2;padding-left:16px;position:relative;white-space:nowrap}
.cat-list li:last-child{border-bottom:none}
.cat-list li::before{content:"";position:absolute;left:3px;top:10px;width:5px;height:5px;background:var(--green)}

/* Product grid */
.card{width:133px;height:191px;background:var(--panel);border:1px solid var(--border)}
.card .thumb{width:131px;height:98px}
.card .name{font-size:9px;line-height:11px;padding:8px 7px 0;height:33px;color:var(--text)}
.card .price{font-size:10px;padding:0 7px;color:var(--muted)}
.card .price b{color:var(--green-text)}
.btn-details{display:inline-block;margin:13px 0 0 7px;font-size:7.5px;font-weight:700;padding:2px 8px;border:1px solid #aaa;border-radius:8px;color:#555;background:#f6f6f6}
.btn-details.primary{background:var(--green);border-color:var(--green);color:var(--white)}

.rule{left:389px;top:927px;width:592px;height:1px;background:#555}
.pager{left:607px;top:946px;display:flex;gap:8px;font-size:10px;color:var(--muted);align-items:center}
.pager .current{background:var(--green);color:var(--white);width:17px;height:16px;text-align:center;line-height:16px}

/* Footer */
.footer{left:0;top:980px;width:1164px;height:220px;background:var(--charcoal);color:var(--white)}
.fcol{top:34px}
.fcol h4{font-size:12.5px;font-weight:700;margin-bottom:14px}
.fcol ul{list-style:none;font-size:10.5px;line-height:16.6px}
.fcol.cats ul{font-size:9.5px;line-height:15.8px}
.social{display:flex;gap:10px;margin-top:10px}
.social span{width:22px;height:22px;border-radius:50%;background:var(--green);display:flex;align-items:center;justify-content:center}
.subscribe h4{margin:14px 0 4px}
.subscribe p{font-size:10.5px}
.sub-form{display:flex;margin-top:7px;border:1px solid var(--green);width:200px;height:20px}
.sub-form .field{flex:1;background:var(--white);color:#999;font-size:10px;padding-left:5px;line-height:18px}
.sub-form .submit{width:48px;background:var(--green);font-size:8.5px;font-weight:700;text-align:center;line-height:18px}
.copyright{left:182px;top:194px;font-size:10.5px;color:#e5e5e5}
</style>
</head>
<body>

<header>
  <div class="abs topbar"></div>
  <div class="abs brand">KanVex</div>
  <div class="abs login">
    <svg width="9" height="12" viewBox="0 0 9 12"><rect x="0.5" y="5" width="8" height="7" rx="1" fill="#444"/><path d="M2 5V3.2a2.5 2.5 0 0 1 5 0V5" fill="none" stroke="#444" stroke-width="1.5"/></svg>
    LOGIN
  </div>
  <div class="abs tagline">“Great Outdoor Gear for<br>Canada’s First Responders”</div>
  <div class="abs serve">
    <ul><li>SEARCH &amp; RESCUE</li><li>COAST GUARD</li><li>NVDK</li><li>FIRE</li><li>MILITARY</li><li>LAW ENFORCEMENT</li></ul>
  </div>
  <nav class="abs mainnav">
    <a class="active">Rescue Gear</a>
    <a style="left:305px">Footwear</a>
    <a style="left:391px">Clothing</a>
    <a style="left:480px">Tents-Mats-Sleeping Bags</a>
    <a style="left:660px">Camping Gear</a>
    <a style="left:779px">Snow Sports</a>
    <a style="left:888px">Brands</a>
  </nav>
</header>

<section>
  <svg class="abs arrow" style="left:143px" width="22" height="44" viewBox="0 0 22 44"><path d="M20 1 2 22l18 21" fill="none" stroke="#cfcfcf" stroke-width="2"/></svg>
  <div class="abs slider">
    <div class="abs slide-photo" role="img" aria-label="Silhouettes of soldiers with rifles against a cloudy golden sky"></div>
    <div class="abs slide-label">Military</div>
  </div>
  <svg class="abs arrow" style="left:992px" width="22" height="44" viewBox="0 0 22 44"><path d="M2 1l18 21L2 43" fill="none" stroke="#cfcfcf" stroke-width="2"/></svg>
</section>

<aside>
  <div class="abs sidebar"></div>
  <svg class="abs" style="left:159px;top:506px" width="26" height="23" viewBox="0 0 26 23"><path d="M0 0h26v23H0l9-11.5z" fill="#3d3d3d"/></svg>
  <div class="abs cat-title">Categories</div>
  <ul class="abs cat-list">
    <li>Rescue Gear</li><li>Footwear</li><li>Clothing</li><li>Tents,Mats,Sleeping Bags</li><li>Camping Gear</li><li>Snow Sports</li><li>Brands</li>
  </ul>
</aside>

<main>
  <div class="abs card" style="left:389px;top:489px">
    <div class="thumb" role="img" aria-label="Product photo: camouflage gaiters over boots" style="background:linear-gradient(180deg,#c9c6b4,#a8a48a)"></div>
    <div class="name">Multiterrain Expedition Gaiters</div>
    <div class="price">Price: <b>$126.00</b></div>
    <span class="btn-details primary">Details→</span>
  </div>
  <div class="abs card" style="left:539px;top:489px">
    <div class="thumb" role="img" aria-label="Product photo: fleece winter hat" style="background:linear-gradient(180deg,#c8d4de,#9aa0a6)"></div>
    <div class="name">Gale Guard Hat™</div>
    <div class="price">Price: <b>$123.00</b></div>
    <span class="btn-details">Details→</span>
  </div>
  <div class="abs card" style="left:694px;top:489px">
    <div class="thumb" role="img" aria-label="Product photo: soldiers in camouflage kneeling with equipment" style="background:linear-gradient(180deg,#8b8062,#5a5240)"></div>
    <div class="name">Weight: 7.63 lbs (3.46 kgs)<br>Halvik Part # 2750</div>
    <div class="price">Price: <b>$420.00</b></div>
    <span class="btn-details">Details→</span>
  </div>
  <div class="abs card" style="left:848px;top:489px">
    <div class="thumb" role="img" aria-label="Product photo: pair of camouflage gloves" style="background:linear-gradient(180deg,#d6cbb8,#b2aa8c)"></div>
    <div class="name">Multiterrain Emberline Gloves</div>
    <div class="price">Price: <b>$339.00</b></div>
    <span class="btn-details">Details→</span>
  </div>

  <div class="abs card" style="left:389px;top:700px">
    <div class="thumb" role="img" aria-label="Product photo: pair of black mitt liners" style="background:linear-gradient(180deg,#8a8a8a,#4a4a4a)"></div>
    <div class="name">Emberline Mitt Liners</div>
    <div class="price">Price: <b>$ 64.00</b></div>
    <span class="btn-details">Details→</span>
  </div>
  <div class="abs card" style="left:539px;top:700px">
    <div class="thumb" role="img" aria-label="Product photo: bivy sack" style="background:linear-gradient(180deg,#e6e4dc,#b8b4a6)"></div>
    <div class="name">Upland Bivy</div>
    <div class="price">Price: <b>$160.00</b></div>
    <span class="btn-details">Details→</span>
  </div>
  <div class="abs card" style="left:694px;top:700px">
    <div class="thumb" role="img" aria-label="Product photo: backpack" style="background:linear-gradient(180deg,#d8dccb,#9ea08a)"></div>
    <div class="name">Drypak Ridge Sack™</div>
    <div class="price">Price: <b>$79.00</b></div>
    <span class="btn-details">Details→</span>
  </div>
  <div class="abs card" style="left:848px;top:700px">
    <div class="thumb" role="img" aria-label="Product photo: camouflage poncho cover" style="background:linear-gradient(180deg,#dcd6c2,#a39a72)"></div>
    <div class="name">Multiterrain Cliffrunner Cover</div>
    <div class="price">Price: <b>$239.00</b></div>
    <span class="btn-details">Details→</span>
  </div>

  <div class="abs rule"></div>
  <div class="abs pager">
    <span class="current">1</span><span>2</span><span>3</span><span>4</span><span>5</span><span>Next &gt;</span><span>&nbsp;Last &gt;&gt;</span>
  </div>
</main>

<footer class="abs footer">
  <div class="abs fcol" style="left:184px">
    <h4>Company</h4>
    <ul><li>Home</li><li>About Us</li><li>Blog</li><li>Latest News</li><li>Login</li><li>Join Us</li></ul>
  </div>
  <div class="abs fcol cats" style="left:351px">
    <h4>Categories</h4>
    <ul><li>Rescue Gear</li><li>Footwear</li><li>Clothing</li><li>Tents,Mats,Sleeping Bags</li><li>Camping Gear</li><li>Snow Sports</li><li>Brands</li></ul>
  </div>
  <div class="abs fcol" style="left:581px">
    <h4>Information</h4>
    <ul><li>My Account</li><li>Rewards</li><li>Terms &amp; Conditions</li><li>Buying Guide</li><li>FAQ</li></ul>
  </div>
  <div class="abs fcol subscribe" style="left:782px;top:30px">
    <h4 style="margin:0">Get in Touch</h4>
    <div class="social">
      <span></span>
      <span></span>
      <span><svg width="11" height="11" viewBox="0 0 11 11"><circle cx="2" cy="9" r="1.5" fill="#fff"/><path d="M1 5a5 5 0 0 1 5 5M1 1a9 9 0 0 1 9 9" fill="none" stroke="#fff" stroke-width="1.6"/></svg></span>
      <span><svg width="12" height="9" viewBox="0 0 12 9"><rect x=".5" y=".5" width="11" height="8" fill="#fff"/><path d="M.5.5 6 5l5.5-4.5" fill="none" stroke="#66cc5e"/></svg></span>
    </div>
    <h4>Subscribe</h4>
    <p>Get free product updates &amp; specials!</p>
    <div class="sub-form"><span class="field">Enter Email</span><span class="submit">SUBMIT</span></div>
  </div>
  <div class="abs copyright">© Copy Right 2014 KanVex &nbsp;|&nbsp; All rights reserved</div>
</footer>

</body>
</html>
```